Envelope Design - Winner can do follow-up business

- Varnoko.com is a Swiss-based online store selling business shirts and accessories for business men
- Please visit the webpage to make yourself familiar with the company. Although the text is in German, with Plimbo translator you should be able to understand the main content.
- Our clients are mainly business men between 30 and 60 years old. Mostly with a high income working in the service industry (banking, insurance, lawyers, etc.). Sometimes there wives purchase the shirts for them ;-)
- The colors and the logo are given, as they are also used for the print materials (please see files in attachment)
- I am running several businesses and often need a talented web designer --> the winner gets substantial follow-up business
your task:
-for our company we need a new envelope design
-It should be simple and modern
-please use one of the logos in the followings.
-suprise me :)

```html
<!DOCTYPE html>
<html lang="en">
<head>
<meta charset="utf-8">
<title>Varnoko Envelope Set</title>
<link rel="stylesheet" href="https://fonts.googleapis.com/css2?family=Lexend+Exa:wght@500&family=Open+Sans:wght@400&display=swap">
<style>
  :root {
    --backdrop: #4d301f;
    --paper: #ffffff;
    --edge: #8a8a8a;
    --brand-red: #e8312a;
    --brand-gold: #e6d46a;
    --ink: #1a1a1a;
    --band-dark: #000000;
  }
  * { margin: 0; padding: 0; box-sizing: border-box; }
  html, body { width: 1200px; height: 953px; overflow: hidden; }
  body {
    background: var(--backdrop);
    position: relative;
    font-family: "Open Sans", Arial, sans-serif;
  }
  .envelope {
    position: absolute;
    background: var(--paper);
    border: 1px solid var(--edge);
  }
  .envelope-back { left: 129px; top: 49px; width: 1005px; height: 400px; }
  .envelope-middle { left: 35px; top: 226px; width: 1005px; height: 473px; }
  .envelope-front {
    left: 144px; top: 435px; width: 1006px; height: 473px;
    border: none;
    border-top: 9px solid var(--band-dark);
    border-bottom: 8px solid var(--brand-red);
    border-left: 1px solid var(--edge);
  }
  .flap { position: absolute; left: 0; top: 0; width: 1005px; height: 170px; }
  .brand-name {
    position: absolute;
    font-family: "Lexend Exa", Arial, sans-serif;
    font-weight: 500;
    white-space: nowrap;
  }
  .envelope-back .brand-name {
    color: var(--brand-red);
    font-size: 40px;
    left: 0; right: 0; text-align: center; top: 40px;
  }
  .envelope-middle .brand-mark {
    position: absolute; left: 492px; top: 44px;
    width: 22px; height: 22px; background: var(--brand-red);
  }
  .envelope-middle .brand-name {
    color: var(--brand-gold);
    font-size: 26px;
    left: 0; right: 0; text-align: center; top: 82px;
  }
  .envelope-front .brand-mark {
    position: absolute; left: 161px; top: 32px;
    width: 34px; height: 34px; background: var(--brand-red);
  }
  .envelope-front .brand-name {
    color: var(--brand-gold);
    font-size: 40px;
    left: 30px; top: 104px;
  }
  .contact {
    position: absolute; bottom: 26px;
    display: flex; align-items: center; gap: 10px;
    font-size: 20px; color: var(--ink);
  }
  .contact svg { width: 22px; height: 24px; }
  .contact-address { left: 28px; }
  .contact-web { right: 28px; }
</style>
</head>
<body>
  <div class="envelope envelope-back">
    <svg class="flap" viewBox="0 0 1005 170" aria-hidden="true">
      <path d="M0,0 C12,45 20,78 80,88 L470,156 Q503,161 536,156 L925,88 C985,78 993,45 1005,0" fill="none" stroke="#555" stroke-width="1"/>
    </svg>
    <div class="brand-name">VARNOKO</div>
  </div>

  <div class="envelope envelope-middle">
    <svg class="flap" viewBox="0 0 1005 170" aria-hidden="true">
      <path d="M0,0 C12,45 20,78 80,88 L470,156 Q503,161 536,156 L925,88 C985,78 993,45 1005,0" fill="none" stroke="#555" stroke-width="1"/>
    </svg>
    <div class="brand-mark"></div>
    <div class="brand-name">VARNOKO</div>
  </div>

  <div class="envelope envelope-front">
    <div class="brand-mark"></div>
    <div class="brand-name">VARNOKO</div>
    <div class="contact contact-address">
      <svg viewBox="0 0 22 24" aria-hidden="true">
        <path d="M11,1 C5.5,1 2,5 2,9.5 C2,15 11,23 11,23 C11,23 20,15 20,9.5 C20,5 16.5,1 11,1 Z" fill="var(--brand-red)"/>
        <circle cx="11" cy="9.5" r="3.3" fill="#fff"/>
      </svg>
      <span>Street Name, City Name, State Zipcode</span>
    </div>
    <div class="contact contact-web">
      <svg viewBox="0 0 24 24" aria-hidden="true" fill="none" stroke="var(--brand-red)" stroke-width="1.5">
        <circle cx="12" cy="12" r="10"/>
        <ellipse cx="12" cy="12" rx="4.5" ry="10"/>
        <line x1="2" y1="12" x2="22" y2="12"/>
        <path d="M4,6.5 H20 M4,17.5 H20"/>
      </svg>
      <span>www.varnoko.com</span>
    </div>
  </div>
</body>
</html>
```